Design a cool print brochure for an NGO / Give your work a global impact!!

Hi,
I provide a full design brief (below, please scroll) and a mood board (attached) to help you visualize inside my head.. ;-)
I am also available to help and have worked many years in advertising; we will understand each other.
Objective:
To design an A4 folded in two presentation brochure for a non-profit consulting agency called Verdomo.
Verdomo works in sustainability and international development = working with NGO’s, governments and private sector on global issues such as global warming, education for all etc.
Strategy:
This document is a first step in developing a communication strategy. It will be distributed during a major international event called the Brightwater Aid Forum.
Objective:
The double objective of the brochure is:
a) to inform the recipient of what Verdomo is, in the shortest time possible.
b) to showcase relevant projects to demonstrate Verdomo experience and expertise.
Target:
Main target:
Existing Verdomo contacts, such as members of development organizations, NGOs, private sector foundations (CSR), regional networks and other development actors.
NB: the main target already has a certain awareness of Verdomo: we will try to minimize text to maximize visual impact and readability.
Secondary target:
Verdomo will also distribute the brochure to new prospects of interest during the Brightwater Forum.
Timing:
We will need to finalize the design and have the files by June 1st to allow time for print before the event.
Content:
The document should be concise, highly readable (no clutter) and include:
1. text (that we will provide)
and
2. visual elements such as images, shapes and info-graphics (that is you).
NB: Verdomo does not have its own image bank; photos will be provided by you.
Format:
A4 folded in half - 4pp A5 - PORTRAIT FORMAT) with an impactful visual in the front, logo, title and headline (please see examples in the mood board attached).
Design elements:
Verdomo does not have yet a visual identity (please see: http://verdomo.org) so there is room for creativity and no graphic chart to follow.
The sector of consulting in international development is rather conservative but our intention is to be disruptive and create a “Wow” effect. We count on you for that!
Therefore, the design should be “structured”, “organized”, “uncluttered” but also “modern”, “impactful”, “highly visual” (think infographic or mind map to describe our services and projects).
Please, take the time to see the attached presentation: I give you guidelines and examples of what we want and what we like.
We are looking forward to seeing your work and I am available for comments, questions and support.
Thank you.
RK
Target Market(s)
The full brief is in the project description: please, scroll through it.
The target market is : our existing clients base, working in sustainable development (read: NGO and Allied Assembly people)
Industry/Entity Type
Ngo
Font styles to use
Requirements
Must have
- - Design and color elements: please, no black and white. Our company website is in black and white and without graphics; we want the brochure to break away from that and start creating our brand identity; so please, show us colors and desing elements (shapes, backgrounds, etc).
- You have a chance to showcase your talent in terms of visual identity: what lines, forms, layout and colors can you come up with and apply throughout the brochure and serve as the visual identity of Verdomo?
- The structure of the document should be:
- - Front cover: design elements + impacful photo (see mood board example attached) +our logo + this headline: "Collective action for sustainable development and impact"
- - Inside front: a graphic representation of "Our Services": such as core activity in the center circle and satellite circles for the services we offer.
- - Inside back:
- 1. Icons and text boxes for "Our projects"
- 2. A world map of the countries where we have worked. Full list of countries is here:
- http://verdomo.org/experience-1
- - Back cover: our contact + logos of partners.
- Our partners are listed here:
- Please use their original logos (ie, in color).
- The design we will select will serve as a basis for a graphic chart...so more work to come...word to the wise ;)
- Please check out our website verdomo.org to see what we do etc.
Nice to have
- Icons to reflect our services: what icons can you come up with to describe "training services", "building networks" or "program management"?
- I give examples in the mood board.
Should not have
- We are open to creativity and want to generate a "Wow" effect.
- Just note that the sector is rather conservative so flashy colors and cartoon like characters should be avoided. Think "earth, global change, Allied Assembly, climate" without going too green (it's overdone). ;-)
- Make us stand out in the NGO world
- Now you.

```html
<!DOCTYPE html>
<html lang="en">
<head>
<meta charset="utf-8">
<title>Verdomo brochure</title>
<link href="https://fonts.googleapis.com/css2?family=Source+Sans+3:wght@400;600;700&family=Roboto+Condensed:wght@500;700&display=swap" rel="stylesheet">
<style>
:root{
  --bg:#f0f0f1;--paper:#ffffff;--navy:#3c4e6c;--ink:#3a3a3a;--grey:#6e6e6e;
  --orange:#e9a12b;--yellow:#f3cb4a;--red:#f15a29;--green:#7cc143;
  --teal:#1d93b4;--pink:#e3197b;--deep:#252a5e;--heading:#2f4a7a;
}
*{margin:0;padding:0;box-sizing:border-box}
html,body{width:865px;height:1200px;overflow:hidden;background:var(--bg)}
body{position:relative;font-family:"Source Sans 3",Arial,sans-serif;color:var(--ink)}
.page{position:absolute;left:44px;width:759px;background:var(--paper)}
.page-cover{top:31px;height:530px}
.page-inside{top:624px;height:530px}
.stripe{position:absolute;left:0;right:0;bottom:0;height:4px;
  background:linear-gradient(90deg,#2a3d8f 0 6%,#e5243b 6% 12%,#4c9f38 12% 18%,#c5192d 18% 24%,#ff3a21 24% 30%,#26bde2 30% 36%,#fcc30b 36% 42%,#a21942 42% 48%,#fd6925 48% 54%,#dd1367 54% 60%,#fd9d24 60% 66%,#bf8b2e 66% 72%,#3f7e44 72% 78%,#0a97d9 78% 84%,#56c02b 84% 90%,#00689d 90% 95%,#e5243b 95% 100%)}
.wordmark{position:absolute;top:30px;font-size:40px;line-height:1;font-weight:600;color:var(--grey);letter-spacing:-.5px}
.band{position:absolute;left:0;right:0;top:80px;height:309px;background:var(--navy)}
.projects{position:absolute;left:15px;top:32px;width:320px;color:#fff}
.projects h2{font-family:"Roboto Condensed",Arial,sans-serif;font-weight:500;color:var(--orange);font-size:13px;margin-bottom:16px}
.projects li{list-style:none;position:relative;padding-left:14px;font-size:8.6px;line-height:1.15;margin-bottom:11px}
.projects li::before{content:"";position:absolute;left:0;top:2px;width:6px;height:6px;background:var(--orange)}
.cover-photo{position:absolute;left:341px;top:6px;width:418px;height:297px;
  background:radial-gradient(circle at 62% 42%,#f4f6fa 0 8%,#9db5d4 22%,#4d6f9c 45%,#1f3553 75%,#101b2c 100%)}
.contact{position:absolute;left:15px;top:400px}
.contact h3{font-family:"Roboto Condensed",Arial,sans-serif;font-weight:500;font-size:14px;color:var(--heading);margin-bottom:12px}
.contact p{display:flex;align-items:center;font-size:14px;color:#444;margin-bottom:10px}
.contact .dot{width:18px;height:18px;border-radius:50%;background:var(--orange);margin-right:12px;position:relative}
.contact .dot::after{content:"";position:absolute;inset:4px;border-radius:50%;background:#fff}
.divider{position:absolute;left:210px;top:397px;width:1px;height:80px;background:#bbb}
.partners{position:absolute;left:232px;top:403px;width:185px}
.partners p{font-size:7.5px;margin-bottom:10px}
.badges{display:flex;flex-wrap:wrap;gap:8px 9px;align-items:center}
.badge{height:20px;border-radius:2px}
.headline{position:absolute;left:452px;top:440px;font-family:"Roboto Condensed",Arial,sans-serif;font-weight:700;color:var(--heading);font-size:17.5px;line-height:1.3}
.head-band{position:absolute;left:0;right:0;top:14px;height:45px;background:var(--navy)}
.head-band h2{position:absolute;top:13px;font-family:"Roboto Condensed",Arial,sans-serif;font-weight:700;color:#fff;font-size:17px}
.copy{position:absolute;font-size:8.6px;line-height:1.38;text-align:justify}
.copy p+p{margin-top:10px}
.world-map{position:absolute;left:13px;top:198px;width:352px;height:178px;
  background:radial-gradient(ellipse at 50% 50%,#dfe6f3 0,#eef2f8 70%,#fff 100%)}
.lists h4{font-size:10px;font-weight:400;color:var(--orange);margin-bottom:5px}
.lists{position:absolute;top:396px;width:180px}
.lists li{list-style:none;position:relative;padding-left:10px;font-size:8.4px;line-height:1.4}
.lists li::before{content:"";position:absolute;left:0;top:4px;width:5px;height:5px;background:var(--orange)}
.service{position:absolute;width:86px;height:59px;border-radius:9px;color:#fff;text-align:center;font-size:6.6px;font-weight:700;line-height:1.2;padding-top:36px;box-shadow:2px 3px 4px rgba(0,0,0,.18)}
.service svg{position:absolute;left:32px;top:8px}
.hub{position:absolute;left:462px;top:237px;width:197px;height:72px;border-radius:36px;border:2px solid var(--navy);background:#fff}
.hub span{position:absolute;inset:6px;border-radius:30px;background:var(--navy);color:#fff;font-size:34px;font-weight:600;text-align:center;line-height:58px}
.links{position:absolute;left:0;top:0}
</style>
</head>
<body>
<section class="page page-cover">
  <div class="wordmark" style="left:13px">Verdomo</div>
  <div class="wordmark" style="left:395px">Verdomo</div>
  <div class="band">
    <div class="projects">
      <h2>PROJECTS:</h2>
      <ul>
        <li>Advising Norvane in the elaboration of their donor diversification strategy.</li>
        <li>Assisting Castrel Foundation with the review of the intervention guide of Cohesia+ and methodological support to conduct policy dialogue at country level (Union-Latin America).</li>
        <li>Conducting the midterm evaluation of the multi-country programme POLDER (strengthening democratic governance and rule of law in Southeast and Eastern Europe) for the Lowlands Rights Council.</li>
        <li>Conceptualizing and implementing policy dialogues at country level for the Union funded programme Climavera+.</li>
        <li>Contributing with content, analysis and facilitation to the Partners Dialogue Forum, a Union funded multi-stakeholder platform.</li>
        <li>Last but not least, contributing to the debate about relevant aspects of the global agenda through different media outlets, universities and think tanks such as La Crónica, Meridian Geo and Instituto Albera.</li>
      </ul>
    </div>
    <div class="cover-photo" role="img" aria-label="Photo looking up through a spiral glass and steel atrium toward a bright skylight"></div>
  </div>
  <div class="contact">
    <h3>CONTACT US</h3>
    <p><span class="dot"></span>info@verdomo.org</p>
    <p><span class="dot"></span>www.verdomo.org</p>
  </div>
  <div class="divider"></div>
  <div class="partners">
    <p>Verdomo supports the work of:</p>
    <div class="badges">
      <span class="badge" style="width:38px;background:#1f3f99"></span>
      <span class="badge" style="width:52px;background:#c8202e"></span>
      <span class="badge" style="width:38px;background:#2a5aa8"></span>
      <span class="badge" style="width:20px;border-radius:50%;background:#6b8fc4"></span>
      <span class="badge" style="width:42px;background:#2d6db5"></span>
      <span class="badge" style="width:38px;background:#8a9aa8"></span>
      <span class="badge" style="width:42px;background:#222"></span>
      <span class="badge" style="width:28px;border-radius:50%;background:#e57373"></span>
    </div>
  </div>
  <div class="headline">PROMOTING COLLECTIVE ACTION<br>FOR SUSTAINABLE DEVELOPMENT</div>
  <div class="stripe"></div>
</section>

<section class="page page-inside">
  <div class="head-band">
    <h2 style="left:15px">OUR FIELD</h2>
    <h2 style="left:391px">OUR SERVICES</h2>
  </div>
  <div class="copy" style="left:15px;top:67px;width:350px">
    <p>Is it possible to deliver effective solutions in the 21st Century without well-managed collaborative action?</p>
    <p>At Verdomo we consider that, both individually and collectively, we are evolving towards more complex and mixed forms of interaction and organization. Our view is that the intellectual effort to understand that evolution needs to be combined with the practical capacity to take advantage of its great potential: the construction of realistic schemes and environments where both citizens and organizations can participate critically and contribute effectively to the public good.</p>
  </div>
  <div class="copy" style="left:392px;top:67px;width:352px">
    <p>Verdomo is a response to the growing need of a wide array of organizations to understand changes in the development landscape, undergo structural changes, improve processes and increase the impact of their participation in collective actions to attain development goals.</p>
  </div>
  <div class="world-map" role="img" aria-label="Dotted world map with pins marking countries where Verdomo has worked"></div>
  <div class="lists" style="left:13px">
    <h4>We specialize in:</h4>
    <ul><li>Policy dialogue</li><li>Donor diversification strategies</li><li>Multi-stakeholder partnerships</li><li>Strategic partnerships</li><li>Coalition building</li><li>Goal-directed networks</li></ul>
  </div>
  <div class="lists" style="left:190px">
    <h4>We work with:</h4>
    <ul><li>International Organizations</li><li>NGOs</li><li>Development agencies</li><li>Trade unions</li><li>Regional and Local governments</li><li>Private sector</li><li>Universities and Think tanks</li></ul>
  </div>

  <svg class="links" width="759" height="530" viewBox="0 0 759 530" aria-hidden="true">
    <g fill="none" stroke="#b9bec8" stroke-width="1.3">
      <path d="M459 207v6h72v12"/><path d="M560 207v18"/><path d="M656 207v6h-72v12"/>
      <path d="M459 343v-6h72v-12"/><path d="M560 343v-18"/><path d="M656 343v-6h-72v-12"/>
      <path d="M485 325a90 55 0 0 1 0-102" stroke="#777"/><path d="M636 325a90 55 0 0 0 0-102" stroke="#777"/>
    </g>
    <g>
      <circle cx="459" cy="207" r="2.5" fill="var(--yellow)"/><circle cx="560" cy="207" r="2.5" fill="var(--red)"/><circle cx="656" cy="207" r="2.5" fill="var(--green)"/>
      <circle cx="531" cy="225" r="2.5" fill="var(--yellow)"/><circle cx="560" cy="225" r="2.5" fill="var(--red)"/><circle cx="584" cy="225" r="2.5" fill="var(--green)"/>
      <circle cx="531" cy="325" r="2.5" fill="var(--teal)"/><circle cx="560" cy="325" r="2.5" fill="var(--pink)"/><circle cx="584" cy="325" r="2.5" fill="var(--deep)"/>
      <circle cx="459" cy="343" r="2.5" fill="var(--teal)"/><circle cx="560" cy="343" r="2.5" fill="var(--pink)"/><circle cx="656" cy="343" r="2.5" fill="var(--deep)"/>
    </g>
  </svg>

  <div class="service" style="left:415px;top:144px;background:var(--yellow)">
    <svg width="22" height="22" viewBox="0 0 22 22"><g fill="none" stroke="#fff" stroke-width="2"><circle cx="11" cy="11" r="9"/><circle cx="11" cy="11" r="4"/></g></svg>RESEARCH AND<br>ANALYSIS</div>
  <div class="service" style="left:523px;top:144px;background:var(--red)">
    <svg width="22" height="22" viewBox="0 0 22 22" fill="#fff"><circle cx="5" cy="8" r="3"/><circle cx="11" cy="6" r="3"/><circle cx="17" cy="8" r="3"/><rect x="1" y="13" width="20" height="6" rx="2"/></svg>FACILITATION AND<br>TRAINING</div>
  <div class="service" style="left:615px;top:144px;background:var(--green)">
    <svg width="22" height="22" viewBox="0 0 22 22"><g fill="none" stroke="#fff" stroke-width="2"><circle cx="8" cy="13" r="5"/><circle cx="16" cy="6" r="3.5"/></g></svg>KNOWLEDGE<br>MANAGEMENT</div>

  <div class="hub"><span>Verdomo</span></div>

  <div class="service" style="left:415px;top:345px;background:var(--teal)">
    <svg width="22" height="22" viewBox="0 0 22 22"><circle cx="11" cy="11" r="10" fill="#fff"/><path d="M11 4v14M4 11h14" stroke="var(--teal)" stroke-width="2"/></svg>COALITION BUILDING</div>
  <div class="service" style="left:523px;top:345px;background:var(--pink)">
    <svg width="22" height="22" viewBox="0 0 22 22" fill="#fff"><rect x="2" y="3" width="18" height="12" rx="1"/><rect x="6" y="17" width="10" height="2"/></svg>EVALUATION</div>
  <div class="service" style="left:615px;top:345px;background:var(--deep)">
    <svg width="22" height="22" viewBox="0 0 22 22"><circle cx="11" cy="11" r="9" fill="none" stroke="#fff" stroke-width="2" stroke-dasharray="4 2"/><circle cx="11" cy="11" r="3" fill="#fff"/></svg>COMMUNICATION</div>

  <div class="copy" style="left:407px;top:454px;width:336px">
    <p>At Verdomo we believe that theory cannot be separated from practice. We provide the necessary tools, methods and skills for public institutions, business and civil society organizations to operate effectively in multi-actor complex environments, whether as part of their internal management process or in the context of their relations with other actors.</p>
  </div>
  <div class="stripe"></div>
</section>
</body>
</html>
```